New Business Card Design Project

We require a business card design for Vexalund, a newly established Indian company.
Our focus is on the development, manufacturing, and export of a diverse array of pharmaceutical products on a global scale. The card should convey a professional appearance, as our primary markets are in Africa, China, and Southeast Asian nations.
We envision a two-sided business card, with the reverse side dedicated to a logo set against a solid color or an elegantly designed pattern. The corners should be rounded. We would appreciate seeing both horizontal and vertical design options. We trust the designer to utilize their expertise in creating this design.

The content for the business card is included in the attached Word file.

Target Market(s)

Our primary markets are in Africa, China, and Southeast Asian, Latin America, Maldives, Sri Lanka

Industry/Entity Type

Pharmaceutical Manufacturing and Export

Contact Information for Business Card

Colors

Designer to choose colors to be used in the design.

Requirements
Must have
• The reverse side of the business card features solely the logo along with the tagline, "Care Without Borders."
Should not have
• The logo should not exceed two instances, encompassing both the front and back sides of the card.

```html
<!DOCTYPE html>
<html lang="en">
<head>
<meta charset="utf-8">
<title>Vexalund Business Card</title>
<link rel="stylesheet" href="https://fonts.googleapis.com/css2?family=Open+Sans:wght@400;600;700&display=swap">
<style>
  :root {
    --stage: #232323;
    --card-dark: #1e1e20;
    --card-blue: #2ea8e0;
    --brand-blue: #2ea8e0;
    --brand-blue-deep: #1b8fcc;
    --brand-coral: #ee5f4c;
    --text-light: #e6e6e6;
    --text-white: #ffffff;
  }
  * { margin: 0; padding: 0; box-sizing: border-box; }
  html, body { width: 1200px; height: 780px; overflow: hidden; background: var(--stage); }
  body {
    font-family: "Open Sans", sans-serif;
    display: flex; align-items: center; justify-content: center; gap: 40px;
  }
  .card {
    position: relative; width: 540px; height: 310px; border-radius: 22px; overflow: hidden;
  }
  .card-front { background: var(--card-dark); }
  .card-back {
    background: var(--card-blue);
    display: flex; flex-direction: column; align-items: center; justify-content: center;
  }

  .brand { display: flex; align-items: center; gap: 10px; }
  .brand-dot { width: 14px; height: 14px; border-radius: 50%; background: var(--brand-coral); }
  .brand-name { font-family: "Open Sans", sans-serif; font-weight: 700; color: var(--brand-blue); }

  .card-front .brand { position: absolute; left: 36px; top: 34px; }
  .card-front .brand-name { font-size: 30px; }

  .address { position: absolute; left: 36px; top: 92px; color: var(--text-light); font-size: 12px; line-height: 1.55; }
  .contacts { position: absolute; left: 36px; top: 146px; list-style: none; color: var(--text-light); font-size: 12px; }
  .contacts li { display: flex; align-items: center; gap: 9px; line-height: 1.9; }
  .contacts svg { width: 12px; height: 12px; flex: none; }

  .person { position: absolute; right: 44px; bottom: 34px; text-align: right; }
  .person-name { font-size: 24px; font-weight: 600; letter-spacing: 0.5px; }
  .person-name .first { color: var(--brand-blue); }
  .person-name .last { color: var(--brand-coral); font-weight: 400; }
  .person-title { color: var(--text-white); font-size: 14px; letter-spacing: 1px; margin-top: 2px; }

  .edge-tab { position: absolute; right: 0; bottom: 36px; width: 22px; height: 46px; background: var(--brand-blue); }

  .card-back .brand-name { color: var(--brand-blue-deep); font-size: 46px; }
  .card-back .brand-dot { background: var(--brand-blue-deep); width: 18px; height: 18px; }
  .tagline { color: var(--text-white); font-size: 14px; margin-top: 8px; letter-spacing: 0.3px; }
</style>
</head>
<body>
  <section class="card card-front" aria-label="Card front">
    <div class="brand">
      <span class="brand-dot"></span>
      <span class="brand-name">Vexalund</span>
    </div>
    <p class="address">14, Sunderban Nagar,<br>Nashik, 422001, India</p>
    <ul class="contacts">
      <li>
        <svg viewBox="0 0 12 12"><rect x="3" y="0.8" width="6" height="10.4" rx="1" fill="none" stroke="#ee5f4c" stroke-width="1.2"/></svg>
        +91 98765 01234
      </li>
      <li>
        <svg viewBox="0 0 12 12"><circle cx="6" cy="6" r="5" fill="none" stroke="#2ea8e0" stroke-width="1.2"/><path d="M1 6h10M6 1c2.5 3 2.5 7 0 10M6 1c-2.5 3-2.5 7 0 10" fill="none" stroke="#2ea8e0" stroke-width="1"/></svg>
        www.vexalund.com
      </li>
      <li>
        <svg viewBox="0 0 12 12"><rect x="0.8" y="2.5" width="10.4" height="7.5" rx="1" fill="none" stroke="#ee5f4c" stroke-width="1.2"/><path d="M1 3l5 4 5-4" fill="none" stroke="#ee5f4c" stroke-width="1.2"/></svg>
        rmalvade@vexalund.com
      </li>
    </ul>
    <div class="person">
      <p class="person-name"><span class="first">Rohan</span> <span class="last">K. Malvade</span></p>
      <p class="person-title">CEO</p>
    </div>
    <span class="edge-tab"></span>
  </section>

  <section class="card card-back" aria-label="Card back">
    <div class="brand">
      <span class="brand-dot"></span>
      <span class="brand-name">Vexalund</span>
    </div>
    <p class="tagline">Care Without Borders.</p>
  </section>
</body>
</html>
```